New Fun, Positive, energised looking Business Card Needed for High Achiever Coach

I am looking for a two sided full colour business card. I am self employed and have recently re branded my 1-2-1 work Renewing Driven Leaders. My target client base for these cards is therefore high achievers - usually aged 40 -55, they are often entrepreneurs, CEO or work in banking and finance and 2/3 are male. I work with them on 90 day or 6 month coaching programs to help them live their success in a healthier, more sustainable and fulfiiled way. They pay for this privately so though they are corporate types the cards need not look 'corporate'. I want to portray the idea of transformation, vitality and re-connecting.
You can get a feel for the look I like on my new website: morvenlisk.co.uk
I want to use this logo with strapline (Renewing Driven Leaders) (I purchased off Logoharbor) and font/ colours (the turquoise and green).
Details to include on the card:
www.morvenlisk.co.uk
+44 7915 302618
morven@morvenlisk.co.uk
skype: morvenlisk
I'd also like to include:
Do you struggle to switch off? Want to be healthier and feel fitter? Want closer relationships? More clarity over the direction you are headed? I can help you do these things using integrated mind-body techniques. Visit morvenlisk.co.uk TODAY to apply for a FREE Breakthrough session.
BUT if that is too much text for a card I am open to advice/ammendments.
Updates
Thanks for your design - I am considering them. PLease change the wording to :

```html
<!DOCTYPE html>
<html lang="en">
<head>
<meta charset="utf-8">
<title>Morven Lisk – Business Card</title>
<link rel="stylesheet" href="https://fonts.googleapis.com/css2?family=Open+Sans:wght@400;600;700;800&display=swap">
<style>
  :root {
    --turquoise: #19a3c9;
    --green: #5ab55a;
    --white: #ffffff;
    --ink: #3b3b3b;
    --rule: #c9c9c9;
    --backdrop: #eceff1;
  }
  * { box-sizing: border-box; margin: 0; padding: 0; }
  html, body {
    width: 1200px; height: 720px; overflow: hidden;
    background: var(--backdrop);
    font-family: "Open Sans", sans-serif;
  }
  .canvas {
    width: 1200px; height: 720px;
    display: flex; align-items: center; justify-content: center; gap: 40px;
  }
  .card {
    position: relative;
    width: 560px; height: 320px;
    overflow: hidden;
    box-shadow: 0 6px 18px rgba(0,0,0,0.12);
  }

  /* Front */
  .card--front { background: var(--white); }
  .front-waves { position: absolute; inset: 0; width: 100%; height: 100%; }
  .wave-green { fill: var(--green); }
  .wave-turquoise { fill: var(--turquoise); }

  .brand {
    position: absolute;
    display: flex; flex-direction: column; align-items: center;
  }
  .brand__row { display: flex; align-items: center; gap: 8px; }
  .brand__dot { width: 16px; height: 16px; border-radius: 50%; }
  .brand__name { font-weight: 800; font-size: 26px; letter-spacing: 0.2px; white-space: nowrap; }
  .brand__strap { font-size: 12px; font-weight: 400; margin-top: 2px; white-space: nowrap; }

  .card--front .brand { left: 50px; top: 88px; width: 200px; }
  .card--front .brand__dot { background: var(--green); }
  .card--front .brand__name,
  .card--front .brand__strap { color: var(--turquoise); }

  .front-divider {
    position: absolute; left: 268px; top: 62px;
    width: 1px; height: 110px; background: var(--rule);
  }
  .contact-list {
    position: absolute; left: 285px; top: 66px;
    list-style: none;
    font-size: 14px; color: var(--ink);
  }
  .contact-list li { display: flex; align-items: center; gap: 8px; height: 27px; }
  .contact-icon { width: 13px; height: 13px; flex: none; }
  .contact-icon--plain {
    width: 12px; height: 12px; border-radius: 50%;
    border: 2px solid var(--turquoise);
  }
  .front-url {
    position: absolute; right: 26px; top: 214px;
    color: var(--white); font-weight: 700; font-size: 16px; letter-spacing: 1.6px;
    white-space: nowrap;
  }

  /* Back */
  .card--back { background: var(--turquoise); color: var(--white); }
  .card--back .brand { left: 34px; top: 124px; width: 210px; }
  .card--back .brand__dot { background: var(--white); }
  .back-divider {
    position: absolute; left: 0; top: 0; width: 100%; height: 100%;
  }
  .back-divider line { stroke: rgba(255,255,255,0.45); stroke-width: 1; }
  .pitch {
    position: absolute; left: 276px; top: 72px; width: 272px;
    font-size: 11.6px; line-height: 1.6;
  }
  .pitch p + p { margin-top: 11px; }
  .pitch strong { font-weight: 700; }
</style>
</head>
<body>
<main class="canvas">

  <section class="card card--front" aria-label="Business card front">
    <svg class="front-waves" viewBox="0 0 560 320" preserveAspectRatio="none" aria-hidden="true">
      <path class="wave-green" d="M0,214 C160,252 330,200 560,136 L560,146 C330,212 160,262 0,225 Z"/>
      <path class="wave-turquoise" d="M0,234 C160,272 330,220 560,156 L560,320 L0,320 Z"/>
    </svg>

    <div class="brand">
      <div class="brand__row">
        <span class="brand__dot" aria-hidden="true"></span>
        <span class="brand__name">Morven Lisk</span>
      </div>
      <span class="brand__strap">Renewing Driven Leaders</span>
    </div>

    <div class="front-divider" aria-hidden="true"></div>

    <ul class="contact-list">
      <li>
        <svg class="contact-icon" viewBox="0 0 16 16" aria-hidden="true">
          <circle cx="8" cy="8" r="7" fill="none" stroke="#19a3c9" stroke-width="1.5"/>
          <path d="M5.5 4.5 L7 4.5 L7.6 6.5 L6.7 7.2 C7.2 8.3 7.9 9 9 9.5 L9.7 8.6 L11.5 9.2 L11.5 10.7 C8 11 5 8 5.5 4.5 Z" fill="#19a3c9"/>
        </svg>
        <span>+44 7915 302618</span>
      </li>
      <li>
        <svg class="contact-icon" viewBox="0 0 16 16" aria-hidden="true">
          <rect x="1" y="3" width="14" height="10" rx="1.5" fill="#19a3c9"/>
          <path d="M1.5 4 L8 9 L14.5 4" fill="none" stroke="#ffffff" stroke-width="1.3"/>
        </svg>
        <span>morven@morvenlisk.co.uk</span>
      </li>
      <li>
        <span class="contact-icon contact-icon--plain" aria-hidden="true"></span>
        <span>morvenlisk</span>
      </li>
    </ul>

    <span class="front-url">www.morvenlisk.co.uk</span>
  </section>

  <section class="card card--back" aria-label="Business card back">
    <svg class="back-divider" viewBox="0 0 560 320" aria-hidden="true">
      <line x1="268" y1="50" x2="250" y2="290"/>
    </svg>

    <div class="brand">
      <div class="brand__row">
        <span class="brand__dot" aria-hidden="true"></span>
        <span class="brand__name">Morven Lisk</span>
      </div>
      <span class="brand__strap">Renewing Driven Leaders</span>
    </div>

    <div class="pitch">
      <p>Do you struggle to switch off?<br>
      Want to be healthier and feel fitter?<br>
      Want closer relationships?<br>
      More clarity over the direction you are headed?</p>
      <p>I can help you do these things using integrated<br>mind-body techniques.</p>
      <p>Visit <strong>morvenlisk.co.uk</strong> TODAY to apply for a<br>FREE Breakthrough session.</p>
    </div>
  </section>

</main>
</body>
</html>
```